Marlowby Services Website Design

We have most content but require a professional design. We have a logo already and will need it utilized along with several of the photos from the attached documentation.
First page should have our mission and Vision and the synapsis provided in the word document. Visitors will be prompted to select from one of our 3 divisions from this page.
Each division will have the same list of tabs : About, Services, Safety, Careers and Contact.
Photos on each divisions page should be representative of the divisions offerings. The word doc attached contains the requested content and we are open to edits that would complement and fill the website.
I like the Quorvane site www.quorvane.example - they are our competition so cant be modeled directly after this.
Please include prompts to request quote at each service page. align the format of the geotechnical page to the other 2 divisions.
I used chat gpt for some of the content so will need it optimized for SCO.

```html
<!DOCTYPE html>
<html lang="en">
<head>
<meta charset="utf-8">
<title>Marlowby Services</title>
<link href="https://fonts.googleapis.com/css2?family=Lato:wght@400;700&family=Oswald:wght@600&family=Michroma&family=Orbitron:wght@800;900&display=swap" rel="stylesheet">
<style>
:root{
  --red:#e5222a;
  --ink:#1b1b1b;
  --muted:#444;
  --panel:#f3f3f3;
  --white:#fff;
  --black:#000;
}
*{margin:0;padding:0;box-sizing:border-box}
html,body{width:1200px;height:3367px;overflow:hidden;background:var(--white)}
body{position:relative;font-family:'Lato',sans-serif;color:var(--ink)}
.abs{position:absolute}
.brand{font-family:'Orbitron',sans-serif;font-weight:900;color:var(--red);letter-spacing:3px;line-height:1}
.btn{position:absolute;background:var(--red);color:var(--white);font-size:14px;display:flex;align-items:center;justify-content:center}
.heading{position:absolute;left:0;width:1200px;text-align:center;font-family:'Orbitron',sans-serif;font-weight:800;color:var(--red);font-size:34px;letter-spacing:1px}

.site-header{position:absolute;left:0;top:0;width:1200px;height:60px;background:var(--white)}
.site-header .brand{position:absolute;left:144px;top:12px;font-size:36px}
.main-nav a{position:absolute;top:22px;font-size:13px;color:var(--ink);text-decoration:none}

.hero{position:absolute;left:0;top:60px;width:1200px;height:550px;background:linear-gradient(180deg,#1f4f86 0%,#3b6ea3 35%,#5f6b4e 62%,#6b5a44 100%)}
.hero h1{position:absolute;left:0;top:44px;width:1200px;text-align:center;font-family:'Oswald',sans-serif;font-weight:600;color:var(--white);font-size:46px;line-height:50px}
.hero p{position:absolute;left:0;top:150px;width:1200px;text-align:center;color:var(--white);font-size:20px}

.service-card{position:absolute;width:296px;height:298px;background:var(--panel);text-align:center}
.service-card svg{position:absolute;left:108px;top:40px}
.service-card h3{position:absolute;left:20px;right:20px;font-family:'Michroma',sans-serif;font-size:15px;font-weight:400;line-height:19px}
.service-card p{position:absolute;left:30px;right:30px;font-size:12.5px;line-height:20.5px;color:var(--ink)}

.about-panel{position:absolute;left:427px;top:1583px;width:773px;height:545px;background:var(--panel)}
.about-photo{position:absolute;left:0;top:1490px;width:554px;height:572px;background:linear-gradient(160deg,#2f4a35 0%,#6f8470 40%,#c9cfcf 60%,#8d8576 100%)}
.about h4{position:absolute;left:653px;font-family:'Michroma',sans-serif;font-weight:400;font-size:26px}
.about p{position:absolute;left:599px;width:450px;font-size:12.5px;line-height:21.6px;color:var(--muted)}

.division{position:absolute;top:2306px;width:282px;height:313px;color:var(--white)}
.division .label{position:absolute;left:17px;font-family:'Michroma',sans-serif;font-size:14px;line-height:17px}
.division .go{position:absolute;width:20px;height:20px;border-radius:50%;background:var(--red)}
.division .go svg{position:absolute;left:4px;top:4px}

.statement{position:absolute;left:0;top:2724px;width:1200px;text-align:center;font-size:25.5px;line-height:32px;font-weight:700;color:var(--ink)}
.statement .brand{font-size:26px;letter-spacing:2px}

.site-footer{position:absolute;left:0;top:2950px;width:1200px;height:367px;background:var(--panel)}
.footer-nav a{position:absolute;top:3149px;font-size:13px;color:var(--ink);text-decoration:none}
.contact-item{position:absolute;top:3240px;font-size:13px;line-height:20px}
.contact-item strong{font-family:'Michroma',sans-serif;font-weight:400;font-size:13px}
.contact-icon{position:absolute;top:3246px;width:30px;height:30px;border:1.5px solid var(--red);border-radius:50%}
.contact-icon svg{position:absolute;left:7px;top:7px}
.legal{position:absolute;left:0;top:3317px;width:1200px;height:50px;background:var(--black);color:var(--white);font-size:12px;display:flex;align-items:center;justify-content:center}
</style>
</head>
<body>

<header class="site-header">
  <div class="brand">MARLOWBY</div>
  <nav class="main-nav">
    <a style="left:644px" href="#">About</a>
    <a style="left:716px" href="#">Services</a>
    <a style="left:801px" href="#">Safety</a>
    <a style="left:874px" href="#">Careers</a>
  </nav>
  <a class="btn" style="left:943px;top:13px;width:117px;height:33px" href="#">Contact Us</a>
</header>

<section class="hero" role="img" aria-label="White aerial lift truck parked on a gravel lot under a blue sky with trees behind">
  <h1>Delivering Safe, Reliable Aerial Access<br>&amp; Maintenance Services</h1>
  <p>To Oil &amp; Gas,Construction, Utility, &amp; Renewable Energy Sector</p>
  <a class="btn" style="left:542px;top:191px;width:116px;height:33px" href="#">Contact Us</a>
</section>

<h2 class="heading" style="top:676px">OUR SERVICES</h2>
<p class="abs" style="left:0;top:730px;width:1200px;text-align:center;font-size:15px">Delivering safe, reliable aerial access and maintenance services</p>

<article class="service-card" style="left:454px;top:771px">
  <svg width="80" height="80" viewBox="0 0 80 80" fill="none" stroke="#e5222a" stroke-width="2"><rect x="8" y="38" width="64" height="36"/><rect x="14" y="12" width="10" height="26"/><rect x="46" y="6" width="14" height="32" rx="7"/><path d="M24 22h22M34 50a6 6 0 1 0 12 0a6 6 0 1 0-12 0M4 74h72"/></svg>
  <h3 style="top:140px">Oil&amp;Gas</h3>
  <p style="top:177px">Lorem ipsum dolor sit amet, consectetur adipiscing elit, sed do eiusmod tempor incididunt ut labore et dolore magna aliqua dolore magna sit</p>
</article>

<article class="service-card" style="left:141px;top:927px">
  <svg width="80" height="80" viewBox="0 0 80 80" fill="none" stroke="#e5222a" stroke-width="2"><circle cx="58" cy="14" r="7"/><path d="M58 2v4M58 22v4M46 14h4M66 14h4"/><path d="M18 60V24c-8 4-10 14-4 20M18 36c8-2 12-10 8-18"/><rect x="34" y="44" width="32" height="20"/><path d="M42 44v20M50 44v20M58 44v20M34 54h32M44 64v10M56 64v10"/></svg>
  <h3 style="top:136px">Renewable Energy<br>Industries</h3>
  <p style="top:189px">Lorem ipsum dolor sit amet, consectetur adipiscing elit, sed do eiusmod tempor incididunt ut labore et dolore magna aliqua dolore magna sit</p>
</article>

<article class="service-card" style="left:765px;top:927px">
  <svg width="80" height="80" viewBox="0 0 80 80" fill="none" stroke="#e5222a" stroke-width="2" style="top:40px"><path d="M34 4h12l2 9 8 3 8-5 8 8-5 8 3 8 9 2v12l-9 2-3 8 5 8-8 8-8-5-8 3-2 9H34l-2-9-8-3-8 5-8-8 5-8-3-8-9-2V34l9-2 3-8-5-8 8-8 8 5 8-3z"/><circle cx="40" cy="40" r="18"/><path d="M32 30v20M48 30v20"/></svg>
  <h3 style="top:140px">Utility</h3>
  <p style="top:177px">Lorem ipsum dolor sit amet, consectetur adipiscing elit, sed do eiusmod tempor incididunt ut labore et dolore magna aliqua dolore magna sit</p>
</article>

<article class="service-card" style="left:454px;top:1081px">
  <svg width="80" height="80" viewBox="0 0 80 80" fill="none" stroke="#e5222a" stroke-width="2"><path d="M6 8h44l14 8H44M30 8v66M20 74l10-50 10 50M22 60h16M26 40h8M4 76h72"/><circle cx="14" cy="64" r="6"/></svg>
  <h3 style="top:140px">Construction</h3>
  <p style="top:177px">Lorem ipsum dolor sit amet, consectetur adipiscing elit, sed do eiusmod tempor incididunt ut labore et dolore magna aliqua dolore magna sit</p>
</article>

<section class="about">
  <div class="about-panel"></div>
  <div class="abs" style="left:433px;top:1479px;width:130px;height:126px;background:var(--red)"></div>
  <div class="about-photo" role="img" aria-label="White lift truck with extended boom parked in front of a forest"></div>
  <div class="brand abs" style="left:591px;top:1628px;font-size:37px">MARLOWBY</div>
  <svg class="abs" style="left:595px;top:1699px" width="40" height="34" viewBox="0 0 40 34" fill="none" stroke="#e5222a" stroke-width="1.8"><path d="M2 17c10-12 26-12 36 0c-10 12-26 12-36 0z"/><circle cx="20" cy="17" r="6"/><circle cx="20" cy="17" r="2"/><path d="M20 2v4M8 6l3 3M32 6l-3 3"/></svg>
  <h4 style="top:1696px">Our Vision</h4>
  <p style="top:1747px">To be the leading provider of aerial access, geotechnical drilling, and service solutions, setting the standard for excellence in safety, efficiency, and environmental stewardship.</p>
  <svg class="abs" style="left:595px;top:1846px" width="40" height="38" viewBox="0 0 40 38" fill="none" stroke="#e5222a" stroke-width="1.8"><circle cx="19" cy="20" r="16"/><circle cx="19" cy="20" r="9"/><circle cx="19" cy="20" r="2"/><path d="M19 20L36 4M30 4h6v6"/></svg>
  <h4 style="top:1845px">Our Mission</h4>
  <p style="top:1901px">At Marlowby, our mission is to deliver unparalleled aerial access, geotechnical drilling, and service and maintenance solutions, consistently exceeding our clients' expectations. We strive to achieve this by investing in cutting-edge technology, fostering a culture of safety and continuous improvement, and prioritizing environmental sustainability. Through collaboration, integrity, and dedication, we aim to contribute to the success of our clients while maintaining the highest standards of quality and professionalism.</p>
</section>

<h2 class="heading" style="top:2208px">OUR DIVISIONS</h2>
<div class="abs" style="left:311px;top:2296px;width:122px;height:119px;background:var(--red)"></div>

<a class="division" style="left:141px;background:linear-gradient(180deg,#1c3350 0%,#2f4a6a 55%,#1a2333 100%)" role="img" aria-label="Aerial lift boom raised beside a wind turbine tower at dusk">
  <span class="label" style="top:183px">Aerial Access</span>
  <span class="abs" style="left:19px;top:211px;width:245px;font-size:11.5px;line-height:20px">Marlowby is a full-service wind energy service provider specializing in blade access &amp; repair , service and maintenance , &amp; trouble shooting on most wind turbine platforms.</span>
  <span class="go" style="left:248px;top:272px"><svg width="12" height="12" viewBox="0 0 12 12" fill="none" stroke="#fff" stroke-width="1.6"><path d="M2 6h8M7 3l3 3-3 3"/></svg></span>
</a>
<a class="division" style="left:459px;background:linear-gradient(180deg,#1d3324 0%,#2e4a2f 50%,#3f5533 100%)" role="img" aria-label="Red tracked geotechnical drilling rig in a green forest clearing">
  <span class="label" style="top:273px">Geotechnical Drilling</span>
  <span class="go" style="left:238px;top:272px"><svg width="12" height="12" viewBox="0 0 12 12" fill="none" stroke="#fff" stroke-width="1.6"><path d="M2 6h8M7 3l3 3-3 3"/></svg></span>
</a>
<a class="division" style="left:779px;background:linear-gradient(200deg,#6d9fd6 0%,#2a5fa6 45%,#143a73 100%)" role="img" aria-label="Wind turbine blades against a deep blue sky">
  <span class="label" style="top:262px">Renewable Energy<br>Services</span>
  <span class="go" style="left:238px;top:272px"><svg width="12" height="12" viewBox="0 0 12 12" fill="none" stroke="#fff" stroke-width="1.6"><path d="M2 6h8M7 3l3 3-3 3"/></svg></span>
</a>

<p class="statement"><span class="brand">MARLOWBY</span> Is A Full-service Wind Energy Service Provider<br>Specializing In Blade Access And Repair, Service And Maintenance,<br>And Trouble Shooting On Most Wind Turbine Platforms.</p>
<a class="btn" style="left:540px;top:2840px;width:116px;height:33px" href="#">Contact Us</a>

<footer>
  <div class="site-footer"></div>
  <div class="brand abs" style="left:0;top:3032px;width:1200px;text-align:center;font-size:34px">MARLOWBY</div>
  <nav class="footer-nav">
    <a style="left:322px" href="#">Home</a>
    <a style="left:414px" href="#">About</a>
    <a style="left:506px" href="#">Services</a>
    <a style="left:611px" href="#">Safety</a>
    <a style="left:704px" href="#">Careers</a>
    <a style="left:807px;font-size:14px" href="#">Contact Us</a>
  </nav>
  <span class="contact-icon" style="left:199px"><svg width="14" height="14" viewBox="0 0 14 14" fill="#e5222a"><path d="M7 0a5 5 0 0 0-5 5c0 4 5 9 5 9s5-5 5-9a5 5 0 0 0-5-5zm0 7a2 2 0 1 1 0-4 2 2 0 0 1 0 4z"/></svg></span>
  <div class="contact-item" style="left:235px">27 Ridgeline Road Harrow Flats<br>Alberta&nbsp; T0X 1Y0</div>
  <span class="contact-icon" style="left:525px"><svg width="14" height="14" viewBox="0 0 14 14" fill="#e5222a"><path d="M3 1l2 3-1.5 1.5a8 8 0 0 0 5 5L10 9l3 2-1 2c-5 0-11-6-11-11z"/></svg></span>
  <div class="contact-item" style="left:567px"><strong>Phone</strong><br>(123)-456-7890</div>
  <span class="contact-icon" style="left:792px"><svg width="14" height="14" viewBox="0 0 14 14" fill="#e5222a"><path d="M1 3h12v8H1z"/><path d="M1 3l6 5 6-5" stroke="#fff" fill="none" stroke-width="1.2"/></svg></span>
  <div class="contact-item" style="left:833px"><strong>Email</strong><br>career@marlowbyservices.example</div>
  <div class="legal">©&nbsp;2024&nbsp;<b>MARLOWBY</b>. All Rights Reserved.</div>
</footer>

</body>
</html>
```